Request for Business Card Design

Hi. My name is Marlene, I am looking for a new business card design for my company, Quarrow Signal Instruments, LLC. I really like the design you did for Tarsel Venture and was hoping you could do something similar using our full logo and our mark. I am also open to any raised texture design using our mark. I have attached our full logo, which would need to be somewhere on the card, as well as the mark in both outline and full form, as well as our brand colors / guide. The card does not have to be white, as long as our logo and mark appear. I actually like darker colored business cards more, but am open to all options. If you are interested in working with me, please let me know. We would also take the business card design into letterhead design if you can do that.

```html
<!DOCTYPE html>
<html lang="en">
<head>
<meta charset="utf-8">
<title>Quarrow Signal Instruments — Business Card</title>
<link href="https://fonts.googleapis.com/css2?family=Open+Sans:wght@400;600;700&display=swap" rel="stylesheet">
<style>
  :root {
    --backdrop: #3b3b3b;
    --card: #141414;
    --card-deep: #0c0c0c;
    --accent: #1aa3d6;
    --ink: #f2f2f2;
    --ink-soft: #d6d6d6;
  }
  * { box-sizing: border-box; margin: 0; padding: 0; }
  html, body { width: 1200px; height: 801px; overflow: hidden; }
  body {
    background: var(--backdrop);
    font-family: "Open Sans", Arial, sans-serif;
    color: var(--ink);
    position: relative;
  }
  .card {
    position: absolute;
    width: 540px;
    height: 309px;
    background: var(--card);
    box-shadow: 0 3px 0 var(--accent), 0 18px 40px rgba(0,0,0,.45);
    overflow: hidden;
  }
  .card--front { left: 40px; top: 246px; }
  .card--back { left: 620px; top: 246px; background: var(--card-deep); }

  .wordmark { position: absolute; display: flex; align-items: center; gap: 14px; }
  .wordmark__dot {
    width: 44px; height: 44px; border-radius: 50%;
    background: var(--accent); flex: none;
  }
  .wordmark__name {
    font-weight: 700; font-size: 36px; letter-spacing: 3px;
    line-height: 1; color: var(--ink); text-transform: uppercase;
  }
  .wordmark__tag {
    font-weight: 700; font-size: 9.5px; letter-spacing: .6px;
    color: var(--ink); text-transform: uppercase; margin-top: 4px;
  }
  .card--front .wordmark { left: 40px; top: 92px; }

  .divider {
    position: absolute; left: 40px; right: 40px; top: 186px;
    height: 1px; background: var(--accent);
  }
  .person { position: absolute; right: 40px; top: 120px; text-align: right; }
  .person__name {
    color: var(--accent); font-weight: 700; font-size: 19px;
    letter-spacing: .5px; text-transform: uppercase;
  }
  .person__role { font-size: 13px; color: var(--ink-soft); margin-top: 1px; }

  .address {
    position: absolute; right: 40px; top: 200px; text-align: right;
    font-size: 13px; line-height: 1.45; color: var(--ink-soft);
  }
  .contacts {
    position: absolute; left: 40px; top: 202px; list-style: none;
    font-size: 13.5px; line-height: 1.6; color: var(--ink-soft);
  }
  .contacts li { display: flex; align-items: center; gap: 9px; }
  .contacts svg { width: 11px; height: 11px; flex: none; fill: var(--ink-soft); }

  .texture {
    position: absolute; inset: 0;
    background: linear-gradient(115deg, #0a0a0a 0%, #111 45%, #2a2a2a 80%, #333 100%);
  }
  .card--back .wordmark { left: 150px; top: 170px; }
  .card--back .wordmark__name { font-size: 38px; }
</style>
</head>
<body>
  <section class="card card--front" aria-label="Business card front">
    <div class="wordmark">
      <span class="wordmark__dot"></span>
      <div>
        <div class="wordmark__name">Quarrow</div>
        <div class="wordmark__tag">Signal Instruments</div>
      </div>
    </div>

    <div class="person">
      <div class="person__name">Devan Holtrey</div>
      <div class="person__role">President</div>
    </div>

    <div class="divider"></div>

    <ul class="contacts">
      <li>
        <svg viewBox="0 0 12 12" aria-hidden="true"><path d="M2.5 1h2l1 2.5-1.3 1a6 6 0 0 0 3.3 3.3l1-1.3L11 7.5v2c0 .8-.7 1.5-1.5 1.5A8.5 8.5 0 0 1 1 2.5C1 1.7 1.7 1 2.5 1z"/></svg>
        555-014-2270
      </li>
      <li>
        <svg viewBox="0 0 12 12" aria-hidden="true"><path d="M1 2.5h10v7H1z M1 2.5l5 4 5-4" fill="none" stroke="#d6d6d6" stroke-width="1.2"/></svg>
        d.holtrey@quarrow.com
      </li>
      <li>
        <svg viewBox="0 0 12 12" aria-hidden="true"><circle cx="6" cy="6" r="4.8" fill="none" stroke="#d6d6d6" stroke-width="1.2"/><path d="M1.2 6h9.6M6 1.2c2.2 2.6 2.2 7 0 9.6M6 1.2c-2.2 2.6-2.2 7 0 9.6" fill="none" stroke="#d6d6d6" stroke-width="1"/></svg>
        www.quarrow.com
      </li>
    </ul>

    <div class="address">
      4172 Bayline Terrace Dr<br>
      Harlow Point CA 90210
    </div>
  </section>

  <section class="card card--back" aria-label="Business card back">
    <div class="texture" role="img" aria-label="Raised spot-gloss pattern of the company mark repeated across the card"></div>
    <div class="wordmark">
      <span class="wordmark__dot"></span>
      <div>
        <div class="wordmark__name">Quarrow</div>
        <div class="wordmark__tag">Signal Instruments</div>
      </div>
    </div>
  </section>
</body>
</html>
```